Sci-Fi Action Novel Cover--"Amber Thaw,"

We need a book cover design (front & back cover) made 1563 x 2500 pixels as a JPEG for the upcoming new science fiction EBook "Amber Thaw," that will published on Pellimar. The book is the third in its series and is a mix of action and romance. We would like the cover's theme to reflect the novel's winter setting.

Please see below Pellimar links to the first two books in the series to get a feel for the previous book covers & story plots, as we would like some of the styles (most text styles) from the first two covers carried over into this cover as well.

http://www.pellimarbooks.example/Tessel-Knight-Stone-Harbor-Book-ebook/dp/Q77K402M19/ref=sr_1_2?ie=UTF8&qid=1839204751&sr=8-2&keywords=tessel+knight

http://www.pellimarbooks.example/Reed-Hollow-Stone-Harbor-Book-ebook/dp/Q77TXN8RZA/ref=sr_1_24?s=books&ie=UTF8&qid=1839204788&sr=1-24&keywords=reed+hollow

The text will run at the top of the cover: Stone Harbor
Book 3
Amber Thaw, (the comma is included)

At the bottom of the page the author's name: Corin T. Baptiste

The image will be photo-realistic and of a young lady with red hair and a red cloak splayed around her as she sits outside in the snow, facing away from the viewer.

The snow-covered lands should be fairly flat & devoid of any other life except for a white man-made observatory tower with a domed top (to show that this isn't taking place in the past or present) rising off in the distance to her right.

The time of day will be just before sunrise, with pretty morning colors (we're not entirely sure which ones yet).

We're looking for the image to be beautiful, & a contrast of vivid colors between the girl & her cloak, the white snow, & the early morning sky.

On the back cover we want the following book description:

"A violent cult, bent on sowing death and chaos across the Tarnic Empire, has fled into Strevan, the empire's sprawling capital city. Hunting them forces Major Oskar Pellu to return to his home city. In a race against time to prevent the crash of his burgeoning career and to protect the people he loves, Oskar and his company of Tarnic rangers must discover and stop the cult's mysterious intentions against the city.

Under the weight of his recent failures and traumas, Oskar struggles to hold back an emotional collapse and to pick up the pieces of his relationship with Rosalind Fairbrook that went cold years ago. Now Oskar must fight for both his mission and the woman who had once loved him in the city he had waited his whole life to get away from."

More info to follow soon about the back cover & spine.

Thank you for your interest

Target Market(s)

Science fiction/action readers

Colors
ffffff
ec1f27
85cae6

Requirements
Must have
• Photo-realistic image (as described above)
• Front & back book cover (with book description on the back)
• Girl facing away, with her hood down so her hair is visible over the cloak
• Fairly clear weather (maybe some clouds if they complement the sunrise, but it should not be snowing)
• Tundra landscape, fairly flat (no trees or mountains, etc.)
• Girl must be fully clothed (this is a winter/tundra scene in the book)
Nice to have
• Carry over in basic styles/layout of previous book covers in the series.
• Nice to have some way for the domed (astronomy/observatory) tower in the distance in order to help signify this is science fiction. (See attachment for basic idea we're thinking of, though the tower for this cover would be taller than the one in the picture)
Should not have
• Any sort of trees or other signs of life on the landscape

```html
<!DOCTYPE html>
<html lang="en">
<head>
<meta charset="utf-8">
<title>Amber Thaw, — Back Cover</title>
<link rel="stylesheet" href="https://fonts.googleapis.com/css2?family=Tinos&display=swap">
<style>
  :root {
    --sky-top: #3a3440;
    --sky-mid: #5a3a4c;
    --cloud-red: #8e3445;
    --cloud-rose: #a45a6a;
    --dusk: #4a3444;
    --snow-shadow: #55576a;
    --snow-light: #8e93a6;
    --snow-deep: #3e4152;
    --text-white: #ffffff;
  }
  html, body {
    margin: 0;
    padding: 0;
    width: 752px;
    height: 1200px;
    overflow: hidden;
    background: var(--sky-top);
  }
  .back-cover {
    position: relative;
    width: 752px;
    height: 1200px;
    overflow: hidden;
  }
  .cover-art {
    position: absolute;
    inset: 0;
    background:
      radial-gradient(ellipse 70% 8% at 40% 62%, rgba(164,90,106,0.55), transparent 70%),
      radial-gradient(ellipse 80% 10% at 55% 22%, rgba(142,52,69,0.7), transparent 70%),
      radial-gradient(ellipse 60% 6% at 30% 34%, rgba(164,90,106,0.5), transparent 70%),
      linear-gradient(180deg,
        var(--sky-top) 0%,
        var(--sky-mid) 10%,
        var(--cloud-red) 20%,
        var(--cloud-rose) 27%,
        var(--dusk) 38%,
        var(--sky-mid) 50%,
        var(--cloud-red) 60%,
        var(--dusk) 66%,
        var(--snow-shadow) 72%,
        var(--snow-light) 82%,
        var(--snow-shadow) 90%,
        var(--snow-deep) 100%);
  }
  .blurb {
    position: absolute;
    left: 68px;
    top: 26px;
    width: 614px;
    font-family: "Tinos", "Times New Roman", serif;
    font-size: 24.5px;
    line-height: 33.5px;
    color: var(--text-white);
    text-align: justify;
    text-shadow: 0 1px 3px rgba(0,0,0,0.45);
  }
  .blurb p {
    margin: 0 0 33px;
  }
</style>
</head>
<body>
  <main class="back-cover">
    <div class="cover-art" role="img" aria-label="Photograph of a pre-dawn winter sky with red and rose clouds over a flat snowy tundra"></div>
    <section class="blurb">
      <p>A violent cult, bent on sowing death and chaos across the Tarnic Empire, has fled into Strevan, the empire’s sprawling capital city. Hunting them forces Major Oskar Pellu to return to his home city. In a race against time to prevent the crash of his burgeoning career and to protect the people he loves, Oskar and his company of Tarnic rangers must discover and stop the cult’s mysterious intentions against the city.</p>
      <p>Under the weight of his recent failures and traumas, Oskar struggles to hold back an emotional collapse and to pick up the pieces of his relationship with Rosalind Fairbrook that went cold years ago. Now Oskar must fight for both his mission and the woman who had once loved him in the city he had waited his whole life to get away from.</p>
    </section>
  </main>
</body>
</html>
```